Home Remodeling company needs a business card design

we need a business card design for home remodeling company in hamilton county, indiana USA. we offers a wide range of construction services including whole house renovations, Design and Build Basements and Kitchen and Bathroom Remodeling . we would like to see designs for both site of business card that use the same color of the company logo and also including all information below :
1- Karim Feltous CEO / General Contractor
2- all company contacts Telephone numbers ( 1-888-DULOM-47 ) ( 317-555-0193) email address ( info@dulomhome.com) website ( www.dulomhome.com ) and social media logos (Facebook- twitter- google plus )
3- company logo
4- licensed . insured . bonded

```html
<!DOCTYPE html>
<html lang="en">
<head>
<meta charset="utf-8">
<title>Dulom Home Remodeling – Business Card</title>
<link rel="stylesheet" href="https://fonts.googleapis.com/css2?family=Open+Sans:wght@400;600&display=swap">
<style>
  :root{
    --stage:#e8e5e0;
    --card-white:#ffffff;
    --charcoal:#333335;
    --charcoal-dark:#2a2a2c;
    --brand-red:#c8313c;
    --text-grey:#4a4a4c;
    --white:#ffffff;
  }
  *{margin:0;padding:0;box-sizing:border-box}
  html,body{width:1200px;height:950px;overflow:hidden}
  body{background:var(--stage);font-family:"Open Sans",sans-serif;position:relative}

  .card{position:absolute;left:250px;width:700px;height:400px;overflow:hidden;
        box-shadow:0 6px 18px rgba(0,0,0,.18)}
  .card--front{top:55px;background:var(--card-white)}
  .card--back{top:495px;background:var(--brand-red)}

  /* front */
  .front__panel{position:absolute;inset:0}
  .company{position:absolute;left:100px;top:150px;display:flex;align-items:center;gap:12px;
        font-weight:600;font-size:44px;line-height:1;color:var(--text-grey);letter-spacing:1px}
  .company__square{width:14px;height:14px;background:var(--text-grey)}
  .person{position:absolute;left:100px;top:248px}
  .person__name{font-size:28px;font-weight:600;color:var(--text-grey);letter-spacing:.5px}
  .person__role{font-size:19px;color:var(--brand-red);margin-top:2px}

  .contact{position:absolute;left:620px;top:200px;width:320px;
        transform:translate(-50%,-50%) rotate(90deg);color:var(--white)}
  .contact__mark{display:flex;align-items:center;gap:10px;margin-bottom:14px;
        font-weight:600;font-size:20px;letter-spacing:1px}
  .contact__mark .sq{width:12px;height:12px;background:var(--white)}
  .contact__list{list-style:none}
  .contact__item{display:flex;justify-content:flex-end;align-items:center;gap:12px;
        font-size:16px;line-height:27px;letter-spacing:.3px}
  .contact__item svg{width:15px;height:15px;fill:none;stroke:var(--white);stroke-width:1.8}

  /* back */
  .back__mark{position:absolute;left:55%;top:50%;transform:translate(-50%,-50%);
        display:flex;align-items:center;gap:14px;color:var(--white);
        font-weight:600;font-size:48px;letter-spacing:2px}
  .back__mark .sq{width:26px;height:26px;background:var(--white)}
  .credentials{position:absolute;left:80px;top:200px;width:330px;
        transform:translate(-50%,-50%) rotate(90deg);color:var(--white);text-align:center}
  .credentials__text{font-size:19px;letter-spacing:1.5px;text-transform:uppercase}
  .credentials__rule{height:1px;background:rgba(255,255,255,.6);margin:10px 20px}
  .social{display:flex;justify-content:flex-start;gap:6px;padding-left:30px}
  .social span{width:15px;height:15px;border-radius:50%;background:var(--white)}
</style>
</head>
<body>

<section class="card card--front" aria-label="Business card front">
  <svg class="front__panel" width="700" height="400" viewBox="0 0 700 400" aria-hidden="true">
    <polygon points="470,400 555,0 700,0 700,400" fill="var(--charcoal)"/>
    <polygon points="470,400 555,0 566,0 481,400" fill="var(--charcoal-dark)"/>
  </svg>

  <div class="company"><span class="company__square"></span>DULOM</div>

  <div class="person">
    <div class="person__name">Karim Feltous</div>
    <div class="person__role">CEO | General Contractor</div>
  </div>

  <div class="contact">
    <div class="contact__mark"><span class="sq"></span>DULOM</div>
    <ul class="contact__list">
      <li class="contact__item">1-888-DULOM-47
        <svg viewBox="0 0 16 16"><path d="M4 2l2 3-1.5 1.5a8 8 0 0 0 5 5L11 10l3 2-1.5 2.5C7 14 2 9 1.5 3.5z"/></svg></li>
      <li class="contact__item">317-555-0193
        <svg viewBox="0 0 16 16"><rect x="4" y="1.5" width="8" height="13" rx="1.5"/><path d="M7 12h2"/></svg></li>
      <li class="contact__item">info@dulomhome.com
        <svg viewBox="0 0 16 16"><rect x="1.5" y="3.5" width="13" height="9"/><path d="M1.5 3.5l6.5 5 6.5-5"/></svg></li>
      <li class="contact__item">www.dulomhome.com
        <svg viewBox="0 0 16 16"><circle cx="8" cy="8" r="6.5"/><path d="M1.5 8h13M8 1.5c3 3.5 3 9.5 0 13M8 1.5c-3 3.5-3 9.5 0 13"/></svg></li>
    </ul>
  </div>
</section>

<section class="card card--back" aria-label="Business card back">
  <div class="credentials">
    <div class="credentials__text">Licensed | Insured | Bonded</div>
    <div class="credentials__rule"></div>
    <div class="social" aria-label="Social media"><span></span><span></span><span></span></div>
  </div>
  <div class="back__mark"><span class="sq"></span>DULOM</div>
</section>

</body>
</html>
```